Business Card Design - ChoiceCraft

Looking for creative, modern design, two sided for ChoiceCraft that is consistent with color and feel of website www.choicecraftpro.net.
Updates

Back of card will be used to promote products or have a quote revolving around decisions, change, leadership, innovation, creativity. Back should also have space to promote website, but optional to use the icon. Front of the card will need to use the icon and have standard place for name, job title, phone and email. We are not looking to put a mailing address or fax. Also want space to place a few words/phrase explaining what we do...such as individual growth and organizational development or tools, training, information...in addition, want the facebook icon small on the front somewhere as we are also on facebook.

Vector file uploaded of icon.

Target Market(s)

Professional coaching for individual growth and organizational development

Industry/Entity Type

Business

Requirements
Must have
• Icon...see attached.

```html
<!DOCTYPE html>
<html lang="en">
<head>
<meta charset="utf-8">
<title>ChoiceCraft Business Card</title>
<link href="https://fonts.googleapis.com/css2?family=Alegreya:wght@400;500&display=swap" rel="stylesheet">
<style>
  :root {
    --page: #ececec;
    --card-dark: #050505;
    --card-light: #ffffff;
    --accent-blue: #1a3fb0;
    --banner-blue: #6fb3ee;
    --icon-blue: #1f6fe0;
    --slate: #2b2b2b;
    --ink: #111111;
    --white: #ffffff;
    --social-bar: #b9d2ee;
    --social-text: #1d3e78;
  }
  * { box-sizing: border-box; margin: 0; padding: 0; }
  html, body { width: 922px; height: 1200px; overflow: hidden; }
  body {
    background: var(--page);
    font-family: "Alegreya", Georgia, serif;
    position: relative;
  }
  .card {
    position: absolute;
    left: 94px;
    width: 808px;
    border-radius: 9px;
    overflow: hidden;
  }

  /* Front */
  .card-front { top: 32px; height: 503px; background: var(--card-dark); color: var(--white); }
  .edge-bar { position: absolute; top: 153px; width: 16px; height: 197px; background: var(--accent-blue); }
  .edge-bar.left { left: 0; }
  .edge-bar.right { right: 0; width: 14px; }
  .brand-mark {
    position: absolute; left: 545px; top: 40px; width: 220px; height: 200px;
    display: flex; align-items: center; gap: 12px;
  }
  .brand-mark .dot { width: 22px; height: 22px; border-radius: 50%; background: var(--banner-blue); flex: none; }
  .brand-mark .name { font-size: 34px; font-weight: 500; color: var(--banner-blue); }
  .name-banner {
    position: absolute; left: 18px; top: 250px; width: 365px; height: 36px;
    background: var(--banner-blue); border-radius: 6px;
    display: flex; align-items: center; padding-left: 34px;
    font-size: 34px; font-weight: 500; color: var(--white); line-height: 1;
  }
  .person { position: absolute; left: 53px; top: 318px; font-size: 20px; line-height: 30px; }
  .contact-icon { position: absolute; left: 47px; width: 46px; height: 46px; }
  .contact-icon.phone { top: 387px; }
  .contact-icon.email { top: 440px; }
  .tagline {
    position: absolute; left: 454px; top: 369px; width: 330px;
    font-size: 20.5px; line-height: 30px; letter-spacing: 0.2px;
  }
  .social-bar {
    position: absolute; left: 454px; top: 469px; width: 312px; height: 18px;
    background: var(--social-bar); display: flex; align-items: center; gap: 6px; padding-left: 4px;
    font-size: 11.5px; font-weight: 500; color: var(--social-text); white-space: nowrap;
  }
  .social-bar .sq { width: 13px; height: 13px; background: var(--social-text); flex: none; }

  /* Back */
  .card-back { top: 570px; height: 528px; background: var(--card-light); }
  .card-back svg.shapes { position: absolute; inset: 0; }
  .back-title {
    position: absolute; left: 64px; top: 118px;
    transform: rotate(-20deg); transform-origin: 0 0;
    font-size: 32px; font-weight: 500; color: var(--white); white-space: nowrap;
  }
  .quotes {
    position: absolute; left: 16px; top: 196px;
    transform: rotate(-20deg); transform-origin: 0 0;
    list-style: none; font-size: 18px; line-height: 29px; color: var(--ink); white-space: nowrap;
  }
  .quotes li::before {
    content: ""; display: inline-block; width: 14px; height: 10px; margin-right: 6px;
    background: var(--ink); vertical-align: 1px;
  }
  .quotes li.cont::before { display: none; }
  .quotes li.cont { padding-left: 42px; }
  .web-address {
    position: absolute; left: 470px; top: 402px;
    transform: rotate(-25deg); transform-origin: 0 0;
    font-size: 22px; line-height: 30px; color: var(--white); white-space: nowrap;
  }
  .corner-name {
    position: absolute; right: 14px; bottom: 14px;
    font-size: 20px; font-weight: 500; color: var(--slate);
  }
</style>
</head>
<body>

<section class="card card-front">
  <div class="edge-bar left"></div>
  <div class="edge-bar right"></div>

  <div class="brand-mark"><span class="dot"></span><span class="name">ChoiceCraft</span></div>

  <div class="name-banner">ChoiceCraft</div>

  <div class="person">
    <p>Name-</p>
    <p>Job Title-</p>
  </div>

  <svg class="contact-icon phone" viewBox="0 0 46 46" aria-label="Phone">
    <circle cx="23" cy="23" r="21" fill="var(--icon-blue)" stroke="#9cc4f5" stroke-width="2"/>
    <path d="M16 13 q-4 3 -1 10 q4 8 12 11 q4 1 6 -2 l-4 -4 q-2 2 -4 0 q-4 -3 -5 -7 q-1 -2 1 -3 z" fill="#ffffff"/>
  </svg>
  <svg class="contact-icon email" viewBox="0 0 46 46" aria-label="Email">
    <circle cx="23" cy="23" r="21" fill="var(--icon-blue)" stroke="#9cc4f5" stroke-width="2"/>
    <rect x="12" y="15" width="22" height="16" fill="#ffffff"/>
    <path d="M12 15 L23 25 L34 15" fill="none" stroke="var(--icon-blue)" stroke-width="2"/>
  </svg>

  <p class="tagline">Providing tools,training,information and collaboration to achieve the results you want.</p>

  <div class="social-bar"><span class="sq"></span>www.linkvine.net/choicecraftpro</div>
</section>

<section class="card card-back">
  <svg class="shapes" viewBox="0 0 808 528" preserveAspectRatio="none">
    <defs>
      <linearGradient id="wedgeTone" x1="0" y1="0" x2="1" y2="1">
        <stop offset="0" stop-color="#3a3a3a"/>
        <stop offset="1" stop-color="#1c1c1c"/>
      </linearGradient>
      <linearGradient id="cornerTone" x1="0" y1="0" x2="1" y2="1">
        <stop offset="0" stop-color="#5a5a5a"/>
        <stop offset="1" stop-color="#b8b8b8"/>
      </linearGradient>
    </defs>
    <polygon points="0,0 498,0 0,182" fill="url(#wedgeTone)"/>
    <line x1="498" y1="0" x2="0" y2="182" stroke="var(--accent-blue)" stroke-width="3"/>
    <polygon points="210,528 808,248 808,528" fill="url(#cornerTone)"/>
    <g transform="rotate(-25 510 400)">
      <rect x="185" y="380" width="650" height="42" rx="9" fill="#000000"/>
      <line x1="185" y1="424" x2="835" y2="424" stroke="var(--accent-blue)" stroke-width="2"/>
    </g>
  </svg>

  <h2 class="back-title">ChoiceCraft</h2>

  <ul class="quotes">
    <li>"Life is not fair - get used to it."</li>
    <li>"Try not to become a man of success, but rather a man of value."</li>
    <li>"We are what we repeatedly do. Excellence is not an act, it is a habit."</li>
    <li>"The measure of a man is the way he bears up under misfortune."</li>
    <li>"My decision to start a new one is just that, a decision, since I never get inspirations."</li>
    <li>"You learn when you listen. You earn when you listen—not just money, but respect."</li>
    <li>"Leadership is a matter of having people look at you and gain confidence, seeing</li>
    <li class="cont">how you react. If you're in control, they're in control."</li>
    <li>"You don't have to reinvent the wheel, just attach it to a new wagon."</li>
    <li>"Every man I meet is my superior in some way."</li>
    <li>"Simplicity is the ultimate sophistication."</li>
  </ul>

  <p class="web-address">www.choicecraftpro.net</p>

  <p class="corner-name">ChoiceCraft</p>
</section>

</body>
</html>
```